Book Cover: Quiet Harbor: Small Ceremonies For The Restless Soul

I would like a full cover spread- front, back and spine as well as a stand alone front cover for Kindle for the book. Design a cover that mirrors the profound depth and dynamic energy of 'Quiet Harbor.' Envision a visual tapestry that draws readers into a transformative journey, where spirituality and self-care unite. Explore vibrant colors, intricate textures, and a sense of inner radiance that beckons readers to explore the book's rich wisdom within. See images for design inspiration attached. Even though some of the images are cartoon, I'd like the cover to be more serious than playful and very elegant.

About this book (back cover copy)
Are you ready to embark on a transformative journey and elevate your daily existence? "Quiet Harbor" is a treasure trove of practical yet profound rituals and wisdom from renowned self-care, healing, and spirituality experts.

Within these pages, you'll uncover a tapestry of guidance and insight from some of the world's most respected mentors. Their collective wisdom is your key to creating a sacred sanctuary within your everyday life.

From invigorating morning rituals to meditative practices, empowering affirmations, and transformative energy healing, you'll find a rich tapestry of tools to nurture a deeper connection with yourself and the universe.

Whether you're a seasoned practitioner or a newcomer to the world of self-care and spirituality, "Quiet Harbor" is your trusted companion on the journey to transform your life and elevate your daily experience. Open this book today and start your sacred, fulfilling adventure.

Colors
0094D4
00A9DD
6FCCEA
C7EBF8
E9F6FB
E54698
E96AAD
F1A4CE
F9D9EA
FCEFF6
6B429C
8869AF
B7A5CE
E3DAEB
F3F0F8

Requirements
Must have
• Title: Quiet Harbor: Subtitle: Small Ceremonies For The Restless Soul Name of Publisher: Lantern Bough Publishing- Logo on the back Back cover copy

```html
<!DOCTYPE html>
<html lang="en">
<head>
<meta charset="utf-8">
<title>Quiet Harbor — Full Cover Spread</title>
<link rel="stylesheet" href="https://fonts.googleapis.com/css2?family=Great+Vibes&family=Crimson+Text:ital,wght@0,400;0,600;1,400&family=Roboto:wght@400;700&display=swap">
<style>
  :root {
    --paper: #fbfcfc;
    --ink: #111111;
    --subtitle-grey: #808080;
    --spine-teal: #2f6f78;
    --gold-light: #f7e27e;
    --gold-mid: #d9b24a;
    --gold-deep: #a9822a;
    --leaf-teal: #5f9e9c;
    --leaf-pale: #d5e7e6;
    --blossom: #f3b6c8;
    --blossom-pale: #fbe3ea;
    --barcode-box: #efefef;
  }
  * { margin: 0; padding: 0; box-sizing: border-box; }
  html, body { width: 1200px; height: 852px; overflow: hidden; background: var(--paper); }
  .spread { position: relative; width: 1200px; height: 852px; background: var(--paper); overflow: hidden; }

  .artwork { position: absolute; }
  .artwork--front-bouquet {
    left: 700px; top: 0; width: 500px; height: 420px;
    background: radial-gradient(ellipse at 80% 25%, var(--blossom) 0%, rgba(243,182,200,0.6) 18%, rgba(95,158,156,0.75) 38%, rgba(213,231,230,0.5) 65%, rgba(251,252,252,0) 82%);
  }
  .artwork--front-sprigs {
    left: 900px; top: 570px; width: 300px; height: 282px;
    background: radial-gradient(ellipse at 65% 60%, rgba(213,231,230,0.7) 0%, rgba(213,231,230,0.3) 45%, rgba(251,252,252,0) 75%);
  }
  .artwork--front-bottom {
    left: 560px; top: 740px; width: 330px; height: 112px;
    background: radial-gradient(ellipse at 50% 100%, rgba(213,231,230,0.8) 0%, rgba(251,252,252,0) 70%);
  }
  .artwork--back-top {
    left: 0; top: 0; width: 560px; height: 230px;
    background: radial-gradient(ellipse at 8% 40%, var(--blossom-pale) 0%, rgba(251,227,234,0.4) 25%, rgba(213,231,230,0.45) 50%, rgba(251,252,252,0) 78%);
  }
  .artwork--back-leaves {
    left: 0; top: 400px; width: 220px; height: 452px;
    background: radial-gradient(ellipse at 20% 75%, var(--leaf-teal) 0%, rgba(95,158,156,0.55) 35%, rgba(213,231,230,0.4) 60%, rgba(251,252,252,0) 85%);
  }

  .script-title {
    position: absolute;
    font-family: "Great Vibes", cursive;
    font-weight: 400;
    line-height: 1;
    padding: 0.35em 0.5em;
    margin: -0.35em -0.5em;
    background: linear-gradient(100deg, var(--gold-light) 0%, var(--gold-mid) 45%, var(--gold-deep) 100%);
    -webkit-background-clip: text; background-clip: text; color: transparent;
    white-space: nowrap;
  }

  /* Back cover */
  .back { position: absolute; left: 0; top: 0; width: 560px; height: 852px; }
  .back .script-title--main { left: 158px; top: 52px; font-size: 120px; }
  .back .script-title--second { left: 216px; top: 132px; font-size: 64px; }
  .back-subtitle {
    position: absolute; left: 40px; width: 490px; top: 204px;
    text-align: center; font-family: "Crimson Text", serif; color: var(--subtitle-grey);
    font-size: 25px; white-space: nowrap;
  }
  .back-subtitle em { font-style: italic; }
  .back-subtitle strong { font-weight: 600; }
  .blurb {
    position: absolute; left: 68px; top: 245px; width: 436px;
    font-family: "Crimson Text", serif; font-size: 15px; line-height: 19.8px;
    color: var(--ink); text-align: center;
  }
  .blurb p + p { margin-top: 19.8px; }
  .blurb strong { font-weight: 600; }
  .blurb em { font-style: italic; }
  .publisher-mark {
    position: absolute; left: 176px; top: 734px; width: 180px; text-align: center;
    font-family: "Crimson Text", serif; font-weight: 400; color: var(--ink);
    font-size: 25px; line-height: 30px;
  }
  .barcode-area { position: absolute; left: 357px; top: 722px; width: 148px; height: 89px; background: var(--barcode-box); }

  /* Spine */
  .spine {
    position: absolute; left: 570px; top: 0; width: 56px; height: 852px;
    writing-mode: vertical-rl; display: flex; align-items: center; justify-content: flex-start;
    padding-top: 30px;
  }
  .spine .script-title--spine { position: relative; font-size: 46px; line-height: 56px; }
  .spine-subtitle {
    font-family: "Crimson Text", serif; color: var(--subtitle-grey);
    font-size: 21px; margin-top: 12px; white-space: nowrap; line-height: 56px;
  }
  .spine-subtitle em { font-style: italic; }
  .spine-publisher {
    font-family: "Roboto", sans-serif; color: var(--spine-teal); font-size: 18px;
    margin-top: 16px; white-space: nowrap; line-height: 56px;
  }
  .spine-publisher strong { font-weight: 700; }

  /* Front cover */
  .front { position: absolute; left: 626px; top: 0; width: 574px; height: 852px; }
  .front .script-title--main { left: 14px; top: 360px; font-size: 200px; }
  .front .script-title--second { left: 118px; top: 520px; font-size: 120px; }
  .front-subtitle {
    position: absolute; left: 40px; width: 480px; top: 672px; text-align: center;
    font-family: "Crimson Text", serif; color: var(--subtitle-grey);
  }
  .front-subtitle .line-italic { display: block; font-style: italic; font-size: 38px; line-height: 42px; }
  .front-subtitle .line-bold { display: block; font-weight: 600; font-size: 40px; line-height: 42px; }
</style>
</head>
<body>
<main class="spread">
  <div class="artwork artwork--back-top" role="img" aria-label="Soft watercolour pink blossoms and pale sage leaves"></div>
  <div class="artwork artwork--back-leaves" role="img" aria-label="Watercolour teal eucalyptus leaves"></div>
  <div class="artwork artwork--front-bouquet" role="img" aria-label="Watercolour bouquet of pink blossoms with deep teal leaves"></div>
  <div class="artwork artwork--front-sprigs" role="img" aria-label="Faint watercolour eucalyptus sprigs"></div>
  <div class="artwork artwork--front-bottom" role="img" aria-label="Pale watercolour leaves"></div>

  <section class="back">
    <h2 class="script-title script-title--main">Quiet</h2>
    <span class="script-title script-title--second">Harbor</span>
    <p class="back-subtitle"><em>Small Ceremonies for</em> <strong>The Restless Soul</strong></p>
    <div class="blurb">
      <p><strong>Are you ready to embark on a transformative journey and elevate your daily existence?</strong> <em>"Quiet Harbor"</em> is a treasure trove of practical yet profound rituals and wisdom from renowned self-care, healing, and spirituality experts.</p>
      <p>Within these pages, you'll uncover a tapestry of guidance and insight from some of the world's most respected mentors. Their collective wisdom is your key to creating a sacred sanctuary within your everyday life.</p>
      <p>From invigorating morning rituals to meditative practices, empowering affirmations, and transformative energy healing, you'll find a rich tapestry of tools to nurture a deeper connection with yourself and the universe.</p>
      <p>Whether you're a seasoned practitioner or a newcomer to the world of self-care and spirituality, "Quiet Harbor" is your trusted companion on the journey to transform your life and elevate your daily experience. Open this book today and start your sacred, fulfilling adventure.</p>
    </div>
    <p class="publisher-mark">Lantern Bough<br>Publishing</p>
    <div class="barcode-area"></div>
  </section>

  <section class="spine">
    <span class="script-title script-title--spine">Quiet Harbor</span>
    <span class="spine-subtitle"><em>Small Ceremonies for</em> The Restless Soul</span>
    <span class="spine-publisher"><strong>Lantern Bough</strong> Publishing</span>
  </section>

  <section class="front">
    <h1 class="script-title script-title--main">Quiet</h1>
    <span class="script-title script-title--second">Harbor</span>
    <p class="front-subtitle">
      <span class="line-italic">Small Ceremonies for</span>
      <span class="line-bold">The Restless</span>
      <span class="line-bold">Soul</span>
    </p>
  </section>
</main>
</body>
</html>
```